House flipping business web site needed

pinecrestholdingsgroup.example.
I am a residential developer in Northern NJ and I am looking for a fresh new updated website. I have an intro video about my company being made now. I don't update it very often but I want an easy format that I can add update photos to on projects I have worked on or homes I renovate for sale.

Target Market(s)

investors into my projects so a portfolio , people looking to sell their homes to me.

Industry/Entity Type

Real Estate Development

Number of Pages Required

4 page

Font styles to use
Serif

Colors
33b8a4
39a9d7
cadf82

Requirements
Must have
• space for an intro video about my company
• a portfolio with pictures and information about each project
• Markets we serve- Morris County, NJ
• My logo- already created
• SEO
• Yes I would like this to function over all platforms. Phone, computer, all platforms.
• history and background page
• I am looking for a completed page that I can upload to the site that hosts my website
Nice to have
• I want something creative, easy to navigate. modern.

```html
<!DOCTYPE html>
<html lang="en">
<head>
<meta charset="utf-8">
<title>Pinecrest Holdings Group</title>
<link href="https://fonts.googleapis.com/css2?family=Raleway:wght@300;400;500&family=Courgette&family=Open+Sans:wght@400;600&family=Roboto:wght@500&display=swap" rel="stylesheet">
<style>
:root{
  --teal:#33b8a4;
  --teal-dark:#2aa593;
  --white:#ffffff;
  --text:#6f6f6f;
  --light-bg:#f1f1f1;
  --nav-text:#555555;
}
*{box-sizing:border-box;margin:0;padding:0}
html,body{width:1200px;height:2791px;overflow:hidden}
body{font-family:"Open Sans",Arial,sans-serif;color:var(--text);background:var(--white);position:relative}
a{text-decoration:none}
.btn{display:inline-flex;align-items:center;justify-content:center;background:var(--teal);color:var(--white);font-family:"Roboto",Arial,sans-serif;font-weight:500;font-size:21px;border-radius:3px}
.topbar{height:41px;background:var(--teal);display:flex;justify-content:flex-end;align-items:center;gap:34px;padding-right:78px;color:var(--white);font-size:17px}
.topbar span{display:flex;align-items:center;gap:10px}
.header{height:95px;position:relative;box-shadow:0 2px 4px rgba(0,0,0,.08)}
.brand{position:absolute;left:90px;top:0;height:95px;display:flex;align-items:center;gap:10px}
.brand-dot{width:22px;height:22px;border-radius:50%;background:var(--teal)}
.brand-name{font-family:"Raleway",sans-serif;font-weight:500;font-size:20px;color:var(--teal);letter-spacing:1px;line-height:1.1}
.nav{position:absolute;top:26px;left:536px;display:flex;align-items:center}
.nav a{font-family:"Raleway",sans-serif;font-size:17px;color:var(--nav-text);text-transform:uppercase;margin-right:50px}
.nav a.active{background:var(--teal);color:var(--white);font-weight:500;width:93px;height:45px;display:flex;align-items:center;justify-content:center;border-radius:3px;margin-right:44px}
.nav .search{position:absolute;left:574px;top:12px}
.hero{position:absolute;top:136px;left:0;width:1200px;height:537px;background:linear-gradient(180deg,#1d3f80 0%,#4a6ea6 30%,#7b6555 55%,#3c4a2a 80%,#4f5a3a 100%);text-align:center}
.hero h1{font-family:"Courgette",cursive;font-weight:400;color:var(--white);font-size:60px;line-height:62px;padding-top:176px;text-shadow:0 2px 6px rgba(0,0,0,.5)}
.hero .btn{position:absolute;left:461px;top:322px;width:270px;height:61px;font-family:"Raleway",sans-serif;font-weight:400;font-size:21px}
.arrow{position:absolute;top:242px;width:52px;height:52px;border:2px solid rgba(255,255,255,.8);border-radius:50%;background:rgba(0,0,0,.25);display:flex;align-items:center;justify-content:center}
.arrow.prev{left:12px}.arrow.next{right:12px}
.welcome{position:absolute;top:673px;width:1200px;text-align:center}
.welcome .emblem{width:70px;height:70px;border-radius:50%;background:var(--teal);margin:42px auto 0}
.section-title{font-family:"Raleway",sans-serif;font-weight:400;color:var(--teal);font-size:42px;text-transform:uppercase}
.welcome .section-title{margin-top:10px}
.welcome p{width:900px;margin:8px auto 0;font-size:13.5px;line-height:27px}
.welcome .btn{width:176px;height:59px;margin-top:15px}
.about{position:absolute;top:1113px;width:1200px;height:441px;background:var(--light-bg)}
.about .section-title{position:absolute;left:78px;top:52px}
.about-text{position:absolute;left:78px;top:112px;width:672px;font-size:13.5px;line-height:27px}
.about-text p+p{margin-top:6px}
.about .btn{position:absolute;left:78px;top:324px;width:177px;height:55px;font-family:"Raleway",sans-serif;font-weight:400;font-size:22px}
.video{position:absolute;left:778px;top:61px;width:344px;height:318px;background:#000}
.video-frame{position:absolute;left:0;top:22px;width:344px;height:274px;background:linear-gradient(180deg,#b9863e 0%,#6f7f55 35%,#3d5e86 60%,#2d4c78 100%)}
.video svg{position:absolute;left:130px;top:110px}
.band{position:absolute;top:1556px;width:1200px;height:258px;background:var(--teal);text-align:center;color:var(--white)}
.band h2{font-family:"Raleway",sans-serif;font-weight:400;font-size:40px;padding-top:38px}
.band p{font-family:"Courgette",cursive;font-size:19px;line-height:28px;margin-top:6px}
.band .outline{position:absolute;left:471px;top:160px;width:270px;height:56px;border:2px solid var(--white);color:var(--white);display:flex;align-items:center;justify-content:center;font-family:"Raleway",sans-serif;font-size:21px;border-radius:3px}
.portfolio{position:absolute;top:1860px;width:1200px;text-align:center}
.portfolio p{width:860px;margin:8px auto 0;font-size:13.5px;line-height:26px}
.grid{position:absolute;top:141px;left:78px;display:grid;grid-template-columns:repeat(4,250px);column-gap:15px;row-gap:24px}
.card{width:250px;height:214px;display:flex;flex-direction:column}
.card .photo{height:158px}
.card .label{height:56px;background:var(--teal);color:var(--white);display:flex;align-items:center;justify-content:space-between;padding:0 18px;font-family:"Raleway",sans-serif;font-size:19px}
.portfolio .btn{position:absolute;left:523px;top:610px;width:154px;height:54px}
.footer{position:absolute;top:2587px;width:1200px;height:204px;background:var(--teal);color:var(--white)}
.fnav{position:absolute;left:78px;top:19px;display:flex;align-items:center;gap:30px;font-size:15px}
.fnav .active{border:1.5px solid var(--white);width:84px;height:44px;display:flex;align-items:center;justify-content:center;border-radius:2px}
.social{position:absolute;right:78px;top:22px;display:flex;gap:8px}
.social span{width:37px;height:37px;border:1.5px solid var(--white);border-radius:50%}
.social span:first-child{background:var(--white)}
.rule{position:absolute;left:78px;right:78px;top:80px;border-top:1px solid rgba(255,255,255,.6)}
.fhead{position:absolute;left:78px;top:98px;font-size:17px;letter-spacing:1px}
.contact{position:absolute;top:128px;display:flex;align-items:center;gap:18px;font-size:13px;line-height:20px;white-space:nowrap}
.contact .ic{width:52px;height:52px;border-radius:50%;background:var(--white);display:flex;align-items:center;justify-content:center;flex:none}
.contact .ic.ring{background:none;border:1.5px solid var(--white)}
.copy{position:absolute;right:78px;top:137px;font-size:13px;line-height:22px;white-space:nowrap}
</style>
</head>
<body>
<div class="topbar">
  <span><svg width="20" height="20" viewBox="0 0 24 24" fill="none" stroke="#fff" stroke-width="2"><path d="M22 16.9v3a2 2 0 0 1-2.2 2 19.8 19.8 0 0 1-8.6-3.1 19.5 19.5 0 0 1-6-6A19.8 19.8 0 0 1 2.1 4.2 2 2 0 0 1 4.1 2h3a2 2 0 0 1 2 1.7c.1 1 .4 1.9.7 2.8a2 2 0 0 1-.5 2.1L8 9.9a16 16 0 0 0 6 6l1.3-1.3a2 2 0 0 1 2.1-.4c.9.3 1.8.6 2.8.7a2 2 0 0 1 1.7 2z"/></svg>123 456 7890</span>
  <span><svg width="22" height="18" viewBox="0 0 24 20" fill="none" stroke="#fff" stroke-width="2"><rect x="2" y="2" width="20" height="16" rx="2"/><path d="M2 4l10 7 10-7"/></svg>info@pinecrestholdingsgroup.example</span>
</div>
<header class="header">
  <div class="brand"><span class="brand-dot"></span><span class="brand-name">PINECREST</span></div>
  <nav class="nav">
    <a class="active" href="#">Home</a><a href="#">About Us</a><a href="#">Portfolio</a><a href="#">Contact Us</a>
    <svg class="search" width="24" height="24" viewBox="0 0 24 24" fill="none" stroke="#33b8a4" stroke-width="3"><circle cx="10" cy="10" r="7"/><path d="M15 15l7 7"/></svg>
  </nav>
</header>
<section class="hero" role="img" aria-label="Large stucco house with tiled roof, palm trees and a brick driveway">
  <h1>We will help you get out of<br>your unwanted home</h1>
  <a class="btn" href="#">CONTACT US KNOW</a>
  <span class="arrow prev"><svg width="16" height="16" viewBox="0 0 16 16" fill="none" stroke="#fff" stroke-width="2"><path d="M11 2L5 8l6 6"/></svg></span>
  <span class="arrow next"><svg width="16" height="16" viewBox="0 0 16 16" fill="none" stroke="#fff" stroke-width="2"><path d="M5 2l6 6-6 6"/></svg></span>
</section>
<section class="welcome">
  <div class="emblem"></div>
  <h2 class="section-title">Welcome to Pinecrest</h2>
  <p>We only buy and renovate homes in our neighborhoods right here in the Morris County, NJ area. Is a house in your neighborhood an eyesore? Is it vacant, boarded up and a hazard to the neighborhood? Please contact us and we can help transform that property into a beautiful home.<br>Do you need to sell your home fast to avoid foreclosure, have estate home you do not want to fix to put on the market, moving for a job and need your house sold fast. We can help. Contact us now.</p>
  <a class="btn" href="#">KNOW MORE</a>
</section>
<section class="about">
  <h2 class="section-title">About Pinecrest</h2>
  <div class="about-text">
    <p>Pinecrest Holdings Group is a family run business with 3rd generation builders and renovators in the Morris County area. As the President and owner of Pinecrest Holdings Group I am dedicated to working hard to create opportunities for investment through real estate.</p>
    <p>At Pinecrest Holdings Group we have a valuable support system and a team of investors, realtors, attorneys, contractors and property managers providing a combined package offering years of experience in the local market. Dana Whitfield-Moore: President and owner<br>Licensed Real Estate Referral Agent</p>
  </div>
  <a class="btn" href="#">KNOW MORE</a>
  <div class="video">
    <div class="video-frame" role="img" aria-label="Intro video still of the owner by a lake with autumn trees"></div>
    <svg width="84" height="84" viewBox="0 0 84 84"><circle cx="42" cy="42" r="40" fill="none" stroke="#33b8a4" stroke-width="3"/><path d="M33 24l28 18-28 18z" fill="#33b8a4"/></svg>
  </div>
</section>
<section class="band">
  <h2>PINECREST</h2>
  <p>We bring excellence to the home buying and renovation business. We will<br>help you get out of your unwanted home</p>
  <a class="outline" href="#">CONTACT US KNOW</a>
</section>
<section class="portfolio">
  <h2 class="section-title">Our Portfolio</h2>
  <p>Many upgrades to this home, Added a new full bath, family room, office, kitchenette and kids play room in walk out basement with 2 triple french doors. New 1/2 bath was added off of the dining room with large.</p>
  <div class="grid">
    <div class="card"><div class="photo" role="img" aria-label="Modern white two storey house" style="background:linear-gradient(180deg,#8fb4de,#d9dcd8 55%,#6e8a4a)"></div><div class="label">PROJECT TITLE<span>&raquo;</span></div></div>
    <div class="card"><div class="photo" role="img" aria-label="Family seated on the front steps of a home" style="background:linear-gradient(180deg,#8a4a3a,#c9b7a4 50%,#9a9a92)"></div><div class="label">PROJECT TITLE<span>&raquo;</span></div></div>
    <div class="card"><div class="photo" role="img" aria-label="White bungalow with garage" style="background:linear-gradient(180deg,#4a86cf,#eaeaea 55%,#7ea25a)"></div><div class="label">PROJECT TITLE<span>&raquo;</span></div></div>
    <div class="card"><div class="photo" role="img" aria-label="Victorian style house on a green lawn" style="background:linear-gradient(180deg,#7aa6d8,#d8cfc0 50%,#5f8a3c)"></div><div class="label">PROJECT TITLE<span>&raquo;</span></div></div>
    <div class="card"><div class="photo" role="img" aria-label="Contemporary cream and brick house" style="background:linear-gradient(180deg,#aac6e4,#e3dcc7 55%,#8f8a7e)"></div><div class="label">PROJECT TITLE<span>&raquo;</span></div></div>
    <div class="card"><div class="photo" role="img" aria-label="Colonial house with wide front lawn" style="background:linear-gradient(180deg,#9cc0e6,#c9c3b8 50%,#6d9446)"></div><div class="label">PROJECT TITLE<span>&raquo;</span></div></div>
    <div class="card"><div class="photo" role="img" aria-label="White gabled house among trees" style="background:linear-gradient(180deg,#6fa0d8,#f0f0ee 55%,#5b8a3a)"></div><div class="label">PROJECT TITLE<span>&raquo;</span></div></div>
    <div class="card"><div class="photo" role="img" aria-label="Hand turning keys in a front door lock" style="background:linear-gradient(90deg,#7a3f22,#c88f68 60%,#e9d8c8)"></div><div class="label">PROJECT TITLE<span>&raquo;</span></div></div>
  </div>
  <a class="btn" href="#">VIEW ALL</a>
</section>
<footer class="footer">
  <nav class="fnav"><a class="active">Home</a><span>About Us</span><span>Portfolio</span><span>Contact Us</span></nav>
  <div class="social"><span></span><span></span><span></span></div>
  <div class="rule"></div>
  <div class="fhead">CONTACT US</div>
  <div class="contact" style="left:78px"><span class="ic"><svg width="22" height="26" viewBox="0 0 24 28"><path d="M12 1a10 10 0 0 0-10 10c0 7 10 16 10 16s10-9 10-16A10 10 0 0 0 12 1z" fill="#33b8a4"/><circle cx="12" cy="11" r="4" fill="#fff"/></svg></span><span>101- Lorem ipsum is dummy<br>text of print and type.</span></div>
  <div class="contact" style="left:340px"><span class="ic ring"><svg width="22" height="22" viewBox="0 0 24 24" fill="#fff"><path d="M22 16.9v3a2 2 0 0 1-2.2 2 19.8 19.8 0 0 1-8.6-3.1 19.5 19.5 0 0 1-6-6A19.8 19.8 0 0 1 2.1 4.2 2 2 0 0 1 4.1 2h3a2 2 0 0 1 2 1.7c.1 1 .4 1.9.7 2.8a2 2 0 0 1-.5 2.1L8 9.9a16 16 0 0 0 6 6l1.3-1.3a2 2 0 0 1 2.1-.4c.9.3 1.8.6 2.8.7a2 2 0 0 1 1.7 2z"/></svg></span><span>123 456 7890</span></div>
  <div class="contact" style="left:540px"><span class="ic ring"><svg width="22" height="18" viewBox="0 0 24 20"><rect x="1" y="2" width="22" height="16" rx="2" fill="#fff"/><path d="M2 4l10 7 10-7" fill="none" stroke="#33b8a4" stroke-width="2"/></svg></span><span>office@pinecrestholdingsgroup.example</span></div>
  <div class="copy">&copy;PINECREST HOLDINGS GROUP<br>2016, All rights reserved.</div>
</footer>
</body>
</html>
```